Copperleaf Roofing Business Card

This is my current business card. But I’d like to make some changes. Somewhere on the card I’d like to list some of the services we offer. Maybe on the back? But I’d still like to keep the red. White and black modern look.

-residential & commercial roofing
-Roof Repairs & Maintenance
-Storm Damage & Insurance Claims specialist
-Christmas Lights and permanent Christmas lights
Fencing. Windows. Gutters. Siding. Sheetrock, painting.

```html
<!DOCTYPE html>
<html lang="en">
<head>
<meta charset="utf-8">
<title>Copperleaf Roofing Co. — Business Card</title>
<link rel="stylesheet" href="https://fonts.googleapis.com/css2?family=Michroma&family=Montserrat:wght@400;500;600&display=swap">
<style>
  :root {
    --stage: #2d2d2d;
    --card-dark: #141414;
    --card-light: #ffffff;
    --brand-red: #e3242b;
    --ink: #161616;
    --ink-soft: #3a3a3a;
    --white: #ffffff;
  }
  * { box-sizing: border-box; margin: 0; padding: 0; }
  html, body {
    width: 1200px; height: 875px; overflow: hidden;
    background: var(--stage);
    font-family: "Montserrat", Arial, sans-serif;
  }
  .stage { position: relative; width: 1200px; height: 875px; }
  .card {
    position: absolute; width: 520px; height: 300px;
    border-radius: 16px; overflow: hidden;
    box-shadow: 0 18px 40px rgba(0,0,0,.45);
  }
  .card--back { left: 50px; top: 170px; background: var(--card-dark); }
  .card--front { left: 630px; top: 405px; background: var(--card-light); }

  /* back side */
  .back-brand {
    position: absolute; inset: 0;
    display: flex; flex-direction: column; align-items: center; justify-content: center; gap: 22px;
  }
  .brand-mark { width: 110px; height: 110px; border-radius: 50%; background: var(--brand-red); }
  .brand-name {
    font-family: "Michroma", "Arial Black", sans-serif;
    font-size: 24px; line-height: 1.3; text-align: center; letter-spacing: 1px;
    color: var(--white);
  }

  /* front side */
  .front-brand { position: absolute; left: 28px; top: 26px; display: flex; align-items: center; gap: 14px; }
  .front-brand .brand-mark { width: 64px; height: 64px; }
  .front-brand .brand-name { font-size: 15px; text-align: left; color: var(--ink); }

  .person { position: absolute; left: 28px; top: 132px; }
  .person-name {
    font-family: "Michroma", "Arial Black", sans-serif;
    font-size: 19px; letter-spacing: 1px; color: var(--ink);
  }
  .person-name .surname { color: var(--brand-red); }
  .person-role { font-size: 12px; color: var(--ink-soft); margin-top: 4px; }

  .contact { position: absolute; left: 28px; top: 200px; list-style: none; }
  .contact li {
    display: flex; align-items: center; gap: 9px;
    font-size: 11.5px; color: var(--ink); margin-bottom: 9px;
  }
  .contact svg { width: 12px; height: 12px; flex: none; }

  .services {
    position: absolute; right: 26px; top: 24px; list-style: none; text-align: right;
  }
  .services li { font-size: 10.5px; line-height: 1.45; color: var(--ink); }
  .services li::after {
    content: ""; display: inline-block; width: 4px; height: 4px; border-radius: 50%;
    background: var(--brand-red); margin-left: 6px; vertical-align: 2px;
  }
  .services li.cont::after { visibility: hidden; }

  .front-emblem {
    position: absolute; right: 36px; bottom: 30px;
    width: 130px; height: 130px; border-radius: 50%; background: var(--brand-red);
  }
</style>
</head>
<body>
<main class="stage">

  <section class="card card--back" aria-label="Card back">
    <div class="back-brand">
      <div class="brand-mark" role="img" aria-label="Company emblem area"></div>
      <p class="brand-name">COPPERLEAF<br>ROOFING CO.</p>
    </div>
  </section>

  <section class="card card--front" aria-label="Card front">
    <div class="front-brand">
      <div class="brand-mark" role="img" aria-label="Company emblem area"></div>
      <p class="brand-name">COPPERLEAF<br>ROOFING CO.</p>
    </div>

    <div class="person">
      <p class="person-name">DEAN <span class="surname">MARSH</span></p>
      <p class="person-role">Owner</p>
    </div>

    <ul class="contact">
      <li>
        <svg viewBox="0 0 24 24" aria-hidden="true"><path fill="var(--brand-red)" d="M6.6 10.8a15.1 15.1 0 0 0 6.6 6.6l2.2-2.2a1 1 0 0 1 1-.25 11.4 11.4 0 0 0 3.6.57 1 1 0 0 1 1 1V20a1 1 0 0 1-1 1A17 17 0 0 1 3 4a1 1 0 0 1 1-1h3.5a1 1 0 0 1 1 1c0 1.25.2 2.45.57 3.57a1 1 0 0 1-.25 1z"/></svg>
        682-555-0143
      </li>
      <li>
        <svg viewBox="0 0 24 24" aria-hidden="true"><path fill="var(--brand-red)" d="M2 5h20v14H2zm2 2v.5l8 5 8-5V7l-8 5z"/></svg>
        dean@copperleafroofing.com
      </li>
      <li>
        <svg viewBox="0 0 24 24" aria-hidden="true"><circle cx="12" cy="12" r="10" fill="var(--brand-red)"/><path d="M2 12h20M12 2c3 3 3 17 0 20M12 2c-3 3-3 17 0 20" stroke="#fff" stroke-width="1.5" fill="none"/></svg>
        www.copperleafroofing.com
      </li>
    </ul>

    <ul class="services">
      <li>residential &amp; commercial roofing</li>
      <li>Roof Repairs &amp; Maintenance</li>
      <li>Storm Damage &amp;</li>
      <li class="cont">Insurance Claims specialist</li>
      <li>Fencing. Windows. Gutters.</li>
      <li class="cont">Siding. Sheetrock, painting</li>
    </ul>

    <div class="front-emblem" role="img" aria-label="Large company emblem area"></div>
  </section>

</main>
</body>
</html>
```